Home Remodeling company needs a business card design

we need a business card design for home remodeling company in hamilton county, indiana USA. we offers a wide range of construction services including whole house renovations, Design and Build Basements and Kitchen and Bathroom Remodeling . we would like to see designs for both site of business card that use the same color of the company logo and also including all information below :
1- Karim Feltous CEO / General Contractor
2- all company contacts Telephone numbers ( 1-888-DULOM-47 ) ( 317-555-0193) email address ( info@dulomhome.com) website ( www.dulomhome.com ) and social media logos (Facebook- twitter- google plus )
3- company logo
4- licensed . insured . bonded

```html
<!DOCTYPE html>
<html lang="en">
<head>
<meta charset="utf-8">
<title>Dulom Home Remodeling – Business Card</title>
<link rel="stylesheet" href="https://fonts.googleapis.com/css2?family=Roboto+Condensed:wght@300;400;700&display=swap">
<style>
  :root {
    --backdrop: #3b3430;
    --card: #1b1b1c;
    --card-edge: #111112;
    --white: #f2f2f2;
    --grey: #c4c4c4;
    --rule: #707070;
    --red: #d3262b;
    --ink: #1b1b1c;
  }
  * { box-sizing: border-box; margin: 0; padding: 0; }
  html, body {
    width: 1200px; height: 787px; overflow: hidden;
    background: var(--backdrop);
    font-family: "Roboto Condensed", "Arial Narrow", sans-serif;
  }
  .sheet {
    position: relative; width: 1200px; height: 787px;
    display: flex; align-items: center; justify-content: center; gap: 60px;
  }
  .card {
    position: relative; width: 520px; height: 297px;
    background: var(--card);
    border: 1px solid var(--card-edge);
    box-shadow: 0 10px 30px rgba(0,0,0,.45);
    color: var(--white);
  }
  .brand { position: absolute; left: 0; right: 0; text-align: center; }
  .brand-name {
    display: block;
    font-weight: 700; font-size: 56px; line-height: 1; letter-spacing: 4px;
    color: var(--white);
  }
  .brand-tagline {
    display: block;
    font-weight: 400; font-size: 14px; letter-spacing: 6px;
    color: var(--white); margin-top: 4px;
  }

  /* back side */
  .card-back .brand { top: 64px; }
  .credentials {
    position: absolute; left: 0; right: 0; top: 176px;
    text-align: center; font-size: 16px; font-weight: 300; color: var(--grey);
    letter-spacing: .5px;
  }
  .back-rule {
    position: absolute; left: 140px; width: 240px; top: 214px; height: 1px;
    background: linear-gradient(90deg, transparent, var(--rule), transparent);
  }
  .social {
    position: absolute; left: 0; right: 0; top: 204px;
    display: flex; justify-content: center; gap: 6px;
  }
  .social-icon {
    width: 20px; height: 20px; border-radius: 50%; background: var(--white);
    display: flex; align-items: center; justify-content: center;
  }
  .social-icon svg { width: 12px; height: 12px; fill: none; stroke: var(--ink); stroke-width: 1.6; }

  /* front side */
  .card-front .brand { top: 60px; left: 120px; right: auto; text-align: left; }
  .person { position: absolute; right: 290px; top: 180px; text-align: right; }
  .person-name { color: var(--red); font-size: 20px; font-weight: 400; }
  .person-title { color: var(--white); font-size: 14px; font-weight: 300; margin-top: 3px; }
  .divider {
    position: absolute; left: 246px; top: 170px; width: 1px; height: 110px;
    background: linear-gradient(180deg, transparent, var(--rule), transparent);
  }
  .contacts { position: absolute; left: 264px; top: 176px; list-style: none; }
  .contacts li {
    display: flex; align-items: center; gap: 12px;
    font-size: 16px; font-weight: 300; line-height: 24px; color: var(--white);
  }
  .contacts svg { width: 14px; height: 14px; flex: none; fill: var(--red); }
</style>
</head>
<body>
<main class="sheet">

  <section class="card card-back" aria-label="Card back">
    <div class="brand">
      <span class="brand-name">DULOM</span>
      <span class="brand-tagline">HOME REMODELING</span>
    </div>
    <p class="credentials">licensed | insured | bonded</p>
    <div class="back-rule"></div>
    <div class="social" aria-label="Social media links">
      <span class="social-icon">
        <svg viewBox="0 0 12 12" aria-hidden="true"><circle cx="3" cy="6" r="1.5"/><circle cx="9" cy="2.5" r="1.5"/><circle cx="9" cy="9.5" r="1.5"/><path d="M4.3 5.3l3.4-2M4.3 6.7l3.4 2"/></svg>
      </span>
      <span class="social-icon">
        <svg viewBox="0 0 12 12" aria-hidden="true"><path d="M2 2.5h8v5.5H5l-2.5 2V8H2z"/></svg>
      </span>
      <span class="social-icon">
        <svg viewBox="0 0 12 12" aria-hidden="true"><path d="M5 7l2-2M4.5 5.5l-1.3 1.3a1.6 1.6 0 0 0 2.3 2.3l1.3-1.3M7.5 6.5l1.3-1.3a1.6 1.6 0 0 0-2.3-2.3L5.2 4.2"/></svg>
      </span>
    </div>
  </section>

  <section class="card card-front" aria-label="Card front">
    <div class="brand">
      <span class="brand-name">DULOM</span>
      <span class="brand-tagline">HOME REMODELING</span>
    </div>

    <div class="person">
      <p class="person-name">Karim Feltous</p>
      <p class="person-title">CEO / General Contractor</p>
    </div>

    <div class="divider"></div>

    <ul class="contacts">
      <li>
        <svg viewBox="0 0 16 16" aria-hidden="true"><path d="M1 5.5C1 3 4 2 8 2s7 1 7 3.5V7h-3.5V5.5h-7V7H1z"/><path d="M4 8h8l2 6H2z"/></svg>
        1-888-DULOM-47
      </li>
      <li>
        <svg viewBox="0 0 16 16" aria-hidden="true"><path d="M4 1h8v14H4zM5.5 3v9h5V3z"/></svg>
        317-555-0193
      </li>
      <li>
        <svg viewBox="0 0 16 16" aria-hidden="true"><path d="M1 3h14v1L8 9 1 4z"/><path d="M1 6l7 5 7-5v7H1z"/></svg>
        info@dulomhome.com
      </li>
      <li>
        <svg viewBox="0 0 16 16" aria-hidden="true"><circle cx="8" cy="8" r="7"/></svg>
        www.dulomhome.com
      </li>
    </ul>
  </section>

</main>
</body>
</html>
```